I need a business card design for a new business based in South West Australia.
I specialize in residential window cleaning & general handyman maintenance.

Dale Marsh - 412 SILVER HAWK DETAILING
- Window Cleaning
- House Maintenance

```html
<!DOCTYPE html>
<html lang="en">
<head>
<meta charset="utf-8">
<title>412 Silver Hawk Detailing – Business Card</title>
<link href="https://fonts.googleapis.com/css2?family=Open+Sans:wght@400;600&display=swap" rel="stylesheet">
<style>
  :root {
    --stage: #e9e7e4;
    --card-light: #ffffff;
    --card-shade: #e6e6e6;
    --ink: #1d1d1d;
    --ink-soft: #3a3a3a;
    --roof-red: #e0565c;
    --wall-grey: #d9d9d9;
  }
  * { margin: 0; padding: 0; box-sizing: border-box; }
  html, body {
    width: 1200px; height: 892px; overflow: hidden;
    background: var(--stage);
    font-family: "Open Sans", Arial, sans-serif;
  }
  .canvas {
    width: 1200px; height: 892px;
    display: flex; align-items: center; justify-content: center;
  }
  .business-card {
    position: relative;
    width: 1000px; height: 580px;
    border-radius: 34px;
    background: radial-gradient(ellipse at 70% 25%, var(--card-light) 0%, #f4f4f4 55%, var(--card-shade) 100%);
    box-shadow: 0 18px 40px rgba(0,0,0,0.18);
    overflow: hidden;
  }
  .company-name {
    position: absolute; left: 70px; top: 62px;
    font-size: 44px; font-weight: 400; letter-spacing: 0.5px;
    color: var(--ink);
  }
  .service-illustration {
    position: absolute; left: 150px; top: 215px;
    width: 380px; height: 330px; border-radius: 24px;
    background: radial-gradient(circle at 58% 38%, var(--roof-red) 0%, #e88d90 22%, var(--wall-grey) 48%, rgba(240,240,240,0) 75%);
  }
  .divider {
    position: absolute; left: 575px; top: 190px;
    width: 2px; height: 360px;
    background: linear-gradient(to bottom, rgba(29,29,29,0) 0%, var(--ink) 20%, var(--ink) 75%, rgba(29,29,29,0) 100%);
  }
  .contact {
    position: absolute; left: 630px; top: 300px;
  }
  .person-name {
    font-size: 40px; font-weight: 600; color: var(--ink);
    margin-bottom: 28px;
  }
  .services { list-style: none; }
  .services li {
    display: flex; align-items: center; gap: 16px;
    font-size: 28px; color: var(--ink-soft);
    margin-bottom: 14px;
  }
  .bullet { width: 14px; height: 14px; flex: none; }
</style>
</head>
<body>
  <main class="canvas">
    <section class="business-card">
      <h1 class="company-name">412 SILVER HAWK DETAILING</h1>
      <div class="service-illustration" role="img" aria-label="Illustration of a handyman in a hard hat repairing a small house with a red roof"></div>
      <div class="divider"></div>
      <div class="contact">
        <p class="person-name">Dale Marsh</p>
        <ul class="services">
          <li><svg class="bullet" viewBox="0 0 14 14"><rect width="14" height="14" fill="#1d1d1d"/></svg>Window Cleaning</li>
          <li><svg class="bullet" viewBox="0 0 14 14"><rect width="14" height="14" fill="#1d1d1d"/></svg>House Maintenance</li>
        </ul>
      </div>
    </section>
  </main>
</body>
</html>
```